Business card design for a teacher - double sided, sleek design.

My name is Lina and I am an online Arabic language teacher. I am looking for a beautiful business card design for my online teaching business.

The cards will be printed in 85mm x 55mm size.
The card can be either portrait or landscape.

The design should contain my logo on one side and information on the other.

The design needs to be clean and modern. Use of subtle Arabic geometric patterns would be nice. Icons for the social media information on the card should also match the design theme.

My logo font is Consolas, which is a Monospace font.

Business card design should be delivered with editable PSD or EPS files in the handover.

Thanks

Lina

----

Information on the back:

URL: www.speakwithnadia.net [this should stand out more than other details]
Email: info@speakwithnadia.net
Instagram: @speakwithnadia
Facebook: facebook.com/speakwithnadia
Skype: speakwithnadia

My brand colours are shown in the logo attached. These are:
- Teal green - 4DC9C1
- Mango yellow - FFD600

Target Market(s)

- Young professionals
- Expatriates
- Women and Men

Industry/Entity Type

Education

Contact Information for Business Card

Information on the back:

Skype: speakwithnadia

- Teal green - 4DC9C1
- Mango yellow - FFD600

Font styles to use
Other font styles liked:
• Any font complimentary to my logo font which is a Monospace font called Consolas.

Colors

Designer to choose colors to be used in the design.

Requirements
Must have
• - Aesthetically pleasing look
• - Complimentary design with existing logo
Nice to have
• Arabic geometrical patterns

```html
<!DOCTYPE html>
<html lang="en">
<head>
<meta charset="utf-8">
<title>Arabic with Lina – Business Card</title>
<link href="https://fonts.googleapis.com/css2?family=Inconsolata:wght@400;600&family=Open+Sans:wght@400;600&display=swap" rel="stylesheet">
<style>
  :root {
    --teal: #4dc9c1;
    --mango: #ffd600;
    --mango-line: #e6c21a;
    --ink: #6f6f6f;
    --ink-dark: #555;
    --paper: #fbfbfb;
    --paper-shade: #eeeeee;
    --stage: #2b2b2b;
  }
  * { box-sizing: border-box; margin: 0; padding: 0; }
  html, body {
    width: 1200px; height: 997px; overflow: hidden;
    background: var(--stage);
  }
  .card {
    position: absolute;
    width: 560px; height: 362px;
    background: var(--paper);
    box-shadow: 0 10px 30px rgba(0,0,0,.45);
    overflow: hidden;
  }
  .card--front { left: 90px; top: 110px; }
  .card--back  { left: 550px; top: 525px; }

  .card__pattern {
    position: absolute; inset: 0;
    background: radial-gradient(circle at 40% 35%, var(--paper) 0%, var(--paper-shade) 100%);
  }

  /* front */
  .brand {
    position: absolute; left: 110px; top: 80px;
    display: flex; align-items: center; gap: 26px;
  }
  .brand__square {
    width: 96px; height: 96px;
    border: 4px solid var(--mango);
  }
  .brand__name {
    font-family: "Inconsolata", monospace;
    font-weight: 400;
    font-size: 46px; letter-spacing: 5px;
    color: var(--ink); text-transform: uppercase;
    line-height: 1.1;
  }
  .rule {
    position: absolute; left: 0; right: 0; height: 3px;
  }
  .card--front .rule { top: 282px; background: var(--teal); }
  .card--back .rule  { top: 282px; background: var(--mango-line); }

  .tag {
    position: absolute; top: 264px; left: 50%;
    transform: translateX(-50%);
    padding: 7px 16px;
    background: var(--paper);
    white-space: nowrap;
  }
  .tag--role {
    border: 3px solid var(--teal);
    font-family: "Open Sans", sans-serif; font-weight: 600;
    font-size: 17px; letter-spacing: 3px; color: var(--ink);
    text-transform: uppercase;
  }
  .tag--web {
    border: 3px solid var(--mango-line);
    font-family: "Open Sans", sans-serif; font-weight: 600;
    font-size: 18px; letter-spacing: 3px; color: var(--teal);
  }

  /* back */
  .contacts {
    position: absolute; left: 150px; top: 70px;
    list-style: none;
    font-family: "Open Sans", sans-serif; font-size: 17px;
    color: var(--ink-dark);
  }
  .contacts__item {
    display: flex; align-items: center; gap: 14px;
    height: 38px;
  }
  .contacts__icon {
    width: 24px; height: 24px; flex: none;
    background: var(--teal);
    display: flex; align-items: center; justify-content: center;
  }
</style>
</head>
<body>

<section class="card card--front">
  <div class="card__pattern" role="img" aria-label="Subtle Arabic geometric lattice pattern in pale grey"></div>
  <div class="brand">
    <div class="brand__square"></div>
    <div class="brand__name">Arabic<br>with Lina</div>
  </div>
  <div class="rule"></div>
  <div class="tag tag--role">Arabic Language Teacher</div>
</section>

<section class="card card--back">
  <div class="card__pattern" role="img" aria-label="Subtle Arabic geometric lattice pattern in pale grey"></div>
  <ul class="contacts">
    <li class="contacts__item"><span class="contacts__icon"></span>/speakwithnadia</li>
    <li class="contacts__item"><span class="contacts__icon"></span>/speakwithnadia</li>
    <li class="contacts__item"><span class="contacts__icon"></span>speakwithnadia.com</li>
    <li class="contacts__item">
      <span class="contacts__icon">
        <svg width="16" height="12" viewBox="0 0 16 12" aria-hidden="true">
          <rect x="0.75" y="0.75" width="14.5" height="10.5" fill="none" stroke="#fff" stroke-width="1.5"/>
          <polyline points="1,1 8,7 15,1" fill="none" stroke="#fff" stroke-width="1.5"/>
        </svg>
      </span>info@speakwithnadia.net</li>
  </ul>
  <div class="rule"></div>
  <div class="tag tag--web">www.speakwithnadia.net</div>
</section>

</body>
</html>
```